Modern HomePage Design for Church

We are looking for a modern homepage design using the sections we put together in the template. The colors we want are blue, black, grey, and white. We do not want use the colors in the logo. Please modify the logo color to match the website color scheme.

Target Market(s)

Church

Industry/Entity Type

Church

Number of Pages Required

1 page

Colors
0293ce
ffffff
474747
9d9d9d

```html
<!DOCTYPE html>
<html lang="en">
<head>
<meta charset="utf-8">
<title>Wellspring Grace Community Church</title>
<link href="https://fonts.googleapis.com/css2?family=Montserrat:wght@400;500;600;700&family=Kaushan+Script&display=swap" rel="stylesheet">
<style>
:root{
  --blue:#0293ce;
  --white:#ffffff;
  --ink:#474747;
  --grey:#9d9d9d;
  --gold:#c9a53a;
  --dark:#1d1d1d;
  --darker:#141414;
  --line:#e4e4e4;
}
*{box-sizing:border-box;margin:0;padding:0}
html,body{width:1200px;height:5248px;overflow:hidden}
body{font-family:"Montserrat",Arial,sans-serif;color:var(--ink);background:var(--white);font-size:15px;line-height:1.6}
section,header,footer{position:relative;width:1200px;overflow:hidden}
.btn{display:inline-block;font-weight:600;font-size:13px;letter-spacing:.5px;text-transform:uppercase;padding:10px 22px;color:var(--white);background:var(--gold)}
.btn-blue{background:var(--blue)}
.btn-dark{background:#111}
.photo{position:absolute}

/* hero */
.hero{height:700px;background:linear-gradient(135deg,#3c3c3c 0%,#242424 45%,#5a5a5a 70%,#2b2b2b 100%)}
.hero .photo{inset:0;background:radial-gradient(ellipse at 70% 40%,rgba(140,140,140,.45),transparent 60%),linear-gradient(160deg,#333,#1f1f1f 60%,#3a3a3a)}
.nav{position:absolute;top:0;left:0;right:0;height:52px;display:flex;align-items:center;padding:0 60px 0 90px;z-index:2}
.nav ul{display:flex;gap:30px;list-style:none;font-size:12px;font-weight:600;color:var(--white)}
.nav .btn{margin-left:auto;padding:16px 24px;font-size:12px}
.brand{position:absolute;top:110px;left:90px;color:var(--white);z-index:2;display:flex;align-items:center;gap:14px}
.brand .dot{width:18px;height:18px;background:var(--blue)}
.brand span{font-size:26px;font-weight:500;line-height:1.05}
.brand small{display:block;font-size:12px;letter-spacing:1px}
.hero .times{position:absolute;top:98px;right:60px;display:flex;gap:24px;z-index:2}
.hero .times .btn{font-size:11px;padding:10px 18px}
.hero-copy{position:absolute;top:300px;left:0;right:0;text-align:center;color:var(--white);z-index:2}
.hero-copy .script{font-family:"Kaushan Script",cursive;font-size:34px}
.hero-copy h1{font-size:64px;font-weight:700;letter-spacing:2px;line-height:1.1;border-bottom:2px solid var(--white);display:inline-block;padding-bottom:6px}
.hero-copy h2{font-size:24px;font-weight:700;margin-top:12px;letter-spacing:1px}
.hero-copy p{font-size:20px;font-weight:700;margin:14px 0 20px}

/* visitor bar */
.visitor{height:77px;background:var(--blue);color:var(--white);display:flex;align-items:center;padding:0 60px 0 36px;font-size:15px;font-weight:600}
.visitor .btn{margin-left:auto}

/* welcome */
.welcome{height:595px;padding:80px 0 0 74px}
.welcome .text{width:560px}
.welcome h2{font-size:44px;font-weight:400;color:#6e6e6e;line-height:1.05;letter-spacing:1px}
.welcome h3{font-size:20px;font-weight:700;color:var(--ink);margin:6px 0 34px}
.welcome p{font-size:15px;margin-bottom:20px}
.welcome .sign{font-family:"Kaushan Script",cursive;font-size:26px;color:#222;border-bottom:1px solid #222;display:inline-block;padding-right:30px;margin-top:10px}
.welcome .photo{top:60px;right:74px;width:470px;height:420px;background:linear-gradient(135deg,#d9d9d9,#8d8d8d 55%,#c4c4c4)}

/* countdown */
.countdown{height:248px;background:var(--dark);color:var(--white);display:flex;align-items:center;padding:0 60px}
.countdown .event{width:520px;text-align:center}
.countdown .event h3{font-size:22px;font-weight:500}
.countdown .event .when{font-size:20px;margin-bottom:24px}
.countdown .event p{font-size:14px;color:#ddd;text-align:left}
.countdown .timer{margin-left:auto;width:480px;text-align:center}
.countdown .cells{display:flex}
.countdown .cell{flex:1;border-left:1px solid #555}
.countdown .cell:first-child{border-left:0}
.countdown .cell small{display:block;font-size:14px;text-transform:uppercase;letter-spacing:1px}
.countdown .cell b{font-size:40px;font-weight:500}
.countdown .btn{margin-top:20px}

/* beliefs */
.beliefs{height:392px;display:flex;justify-content:space-between;padding:80px 60px 0}
.beliefs .col{width:330px;text-align:center}
.beliefs svg{width:80px;height:80px;margin-bottom:40px}
.beliefs h4{font-size:15px;font-weight:700;color:#222}
.beliefs p{font-size:15px;line-height:1.5}

/* involved */
.involved{height:475px;display:flex}
.involved .grid{position:relative;width:700px;height:475px}
.tile{position:absolute;display:flex;align-items:center;justify-content:center}
.tile span{color:var(--white);font-size:12px;font-weight:700;text-transform:uppercase;background:rgba(0,0,0,.45);padding:4px 8px}
.involved .panel{flex:1;background:var(--dark);color:var(--white);padding:160px 60px 0 50px}
.involved h2{font-size:44px;font-weight:400;letter-spacing:1px}
.involved p{font-size:15px;color:#ccc;margin-top:14px}

/* blog */
.blog{height:522px;display:flex}
.blog .text{width:540px;padding:90px 0 0 74px}
.blog h2{font-size:44px;font-weight:400;letter-spacing:1px}
.blog .date{font-size:14px;margin:20px 0 24px}
.blog h3{font-size:19px;color:var(--blue);font-weight:600}
.blog p{font-size:15px;margin-bottom:24px}
.blog .photo{position:static;flex:1;background:radial-gradient(circle at 60% 85%,#f0c25a 0%,#d07a2a 25%,#5a3a2a 55%,#1e1a18 90%)}

/* pastor & podcast */
.pastor{height:501px;background:var(--dark);color:var(--white);padding:70px 74px 0;display:flex}
.pastor h2{font-size:26px;font-weight:500;margin-bottom:26px;letter-spacing:1px}
.pastor .left{width:720px}
.pastor .row{display:flex;gap:30px}
.pastor .portrait{position:static;width:320px;height:320px;background:linear-gradient(160deg,#8aa1ad,#5d6b71 55%,#a98f78)}
.pastor blockquote{width:310px}
.pastor blockquote h3{font-size:30px;font-weight:400;line-height:1.2}
.pastor blockquote p{font-size:14px;color:#ddd;margin:8px 0 20px}
.pastor blockquote cite{font-size:14px;color:#bbb;font-style:normal}
.podcast{margin-left:auto;width:330px}
.podcast li{list-style:none;display:flex;gap:16px;align-items:flex-start;margin-bottom:38px}
.podcast svg{width:30px;height:30px;flex:none}
.podcast b{display:block;font-size:15px;font-weight:500}
.podcast small{font-size:14px;color:#bbb}

/* events */
.events{height:857px;padding:75px 74px 0}
.events h2{text-align:center;font-size:38px;font-weight:400;color:#222;letter-spacing:2px;margin-bottom:50px}
.event-row{display:flex;align-items:flex-start;padding:20px 0 40px;border-bottom:1px solid var(--line);margin-bottom:28px}
.event-row:last-child{border-bottom:0}
.datebox{width:200px;height:110px;background:#3a3a3a;color:var(--white);display:flex;align-items:center;gap:20px;padding:0 22px;flex:none}
.datebox svg{width:40px;height:40px}
.datebox b{font-size:36px;font-weight:400;line-height:1}
.datebox sup{font-size:16px}
.datebox small{display:block;font-size:17px}
.event-row .info{margin-left:45px;flex:1}
.event-row h3{font-size:19px;font-weight:600;color:#222;margin-bottom:12px}
.event-row .meta{font-size:14px;display:flex;align-items:center;gap:10px;line-height:1.9}
.event-row .meta svg{width:14px;height:14px}
.event-row .btn{margin-top:10px}

/* footer */
.footer{height:525px;background:var(--darker);color:var(--white);display:flex;justify-content:space-between;padding:70px 74px 0}
.footer .col{width:310px}
.footer h4{font-size:18px;font-weight:500;margin-bottom:26px}
.item{display:flex;gap:14px;margin-bottom:26px}
.thumb{position:static;width:100px;height:90px;flex:none}
.item b{display:block;color:var(--blue);font-size:14px;font-weight:500}
.item p{font-size:14px;line-height:1.4}
.tags{display:flex;flex-wrap:wrap;gap:8px;margin-bottom:30px}
.tags span{background:var(--blue);font-size:13px;padding:6px 14px}
.feed{position:relative;width:320px;height:180px;background:linear-gradient(160deg,#6a6a6a,#2a2a2a);display:flex;align-items:center;justify-content:center;font-size:20px}

/* bottom */
.bottom{height:280px;display:flex;align-items:center;padding:0 80px 0 74px}
.bottom .brand{position:static;color:#222}
.bottom .social{display:flex;gap:10px;margin-top:14px}
.bottom .social i{width:22px;height:22px;border:1px solid var(--grey);border-radius:50%}
.bottom ul{margin-left:auto;display:flex;gap:28px;list-style:none;font-size:13px;font-weight:600;color:#222;align-items:center}
.bottom .btn{margin-left:20px;padding:14px 22px}
.copyright{height:68px;background:var(--white);border-top:1px solid var(--line);text-align:center;font-size:11px;font-weight:600;color:#222;line-height:68px}
</style>
</head>
<body>

<header class="hero">
  <div class="photo" role="img" aria-label="Close-up of an engraved stone with Easter scripture"></div>
  <nav class="nav">
    <ul><li>HOME</li><li>TEAM</li><li>FEATURES</li><li>EVENTS</li><li>SERMONS</li><li>CONTACT</li><li>BLOG</li></ul>
    <span class="btn btn-blue">Give Online</span>
  </nav>
  <div class="brand"><i class="dot"></i><span>WELLSPRING<small>GRACE COMMUNITY CHURCH</small></span></div>
  <div class="times"><span class="btn">Sunday Worship 10:15</span><span class="btn">Sunday School 09:00</span></div>
  <div class="hero-copy">
    <div class="script">A very special celebration is near</div>
    <h1>EASTER WEEK</h1>
    <h2>JOIN THE REMEMBERANCE</h2>
    <p>Service starting at 19:00 daily</p>
    <span class="btn">Continue Reading</span>
  </div>
</header>

<section class="visitor">
  First time visitor? Find out how, where and when we worship. We hope to see you soon.
  <span class="btn btn-dark">Visitors Info</span>
</section>

<section class="welcome">
  <div class="text">
    <h2>WELCOME TO</h2>
    <h3>WELLSPRING GRACE COMMUNITY CHURCH</h3>
    <p>Lorem ipsum dolor sit amet, consectetur adipiscing elit, sed do eius mod tempor incididunt ut labore et dolore magna ali qua. Ut enim ad minim veniam, quis nostrud exercitation ulla co laboris nisi ut aliquip ex ea commodo consequat.</p>
    <p>Duis aute irure dolor in reprehenderit in voluptate velit esse cillum dolore eu fugiat nulla pariatur.</p>
    <span class="sign">Pastor Daniel</span>
  </div>
  <div class="photo" role="img" aria-label="Black and white photo of an elderly couple embracing"></div>
</section>

<section class="countdown">
  <div class="event">
    <h3>Church leaders meeeting</h3>
    <div class="when">March 27, 2019 - 07:00 pm</div>
    <p>Meeting for the church leaders. This is where we plan the strategy for the church and give feedback on projects.</p>
  </div>
  <div class="timer">
    <div class="cells">
      <div class="cell"><small>Days</small><b>06</b></div>
      <div class="cell"><small>Hours</small><b>15</b></div>
      <div class="cell"><small>Minutes</small><b>26</b></div>
      <div class="cell"><small>Seconds</small><b>16</b></div>
    </div>
    <span class="btn">Read More</span>
  </div>
</section>

<section class="beliefs">
  <div class="col">
    <svg viewBox="0 0 80 80" fill="none" stroke="#777" stroke-width="3"><path d="M40 6v16M33 12h14M20 40l20-18 20 18M24 36v36h32V36M35 72V56h10v16"/></svg>
    <h4>WHAT WE BELIEVE</h4>
    <p>We believe in the existence of GOD and His Holy Word to be the foundation of our faith. It shall not be moved nor be compromised.</p>
  </div>
  <div class="col">
    <svg viewBox="0 0 80 80" fill="none" stroke="#777" stroke-width="3"><path d="M40 10C28 10 20 19 20 30c0 16 20 38 20 38s20-22 20-38c0-11-8-20-20-20z"/><circle cx="40" cy="30" r="7"/></svg>
    <h4>SERVICES &amp; LOCATIONS</h4>
    <p>Riverside, GA 30410, USA<br>Sunday morning (08:15 - 12:00 PM<br>Sunday afternoon (04:00 - 06:00 PM)<br>Wednesday (05:00 - 09:00 PM)</p>
  </div>
  <div class="col">
    <svg viewBox="0 0 80 80" fill="none" stroke="#777" stroke-width="3"><rect x="12" y="16" width="56" height="38"/><path d="M32 54l-4 12h24l-4-12"/></svg>
    <h4>WATCH LIVE</h4>
    <p>By God's grace, we are glad to deliver an online live streaming just for you. Join us by watching live every Sunday and Wednesday</p>
  </div>
</section>

<section class="involved">
  <div class="grid">
    <div class="tile" style="left:0;top:0;width:233px;height:238px;background:linear-gradient(150deg,#7d9bb0,#4f6a4a)" role="img" aria-label="Children at a kids ministry activity"><span>Kids Ministry</span></div>
    <div class="tile" style="left:233px;top:0;width:234px;height:238px;background:linear-gradient(150deg,#9a9a9a,#4a4a4a)" role="img" aria-label="Black and white photo of an outreach visit"><span>Outreach</span></div>
    <div class="tile" style="left:467px;top:0;width:233px;height:238px;background:linear-gradient(150deg,#d9b98c,#8b6a4a)" role="img" aria-label="Teenagers smiling together"><span>Teens Ministry</span></div>
    <div class="tile" style="left:0;top:238px;width:310px;height:237px;background:linear-gradient(150deg,#5a4632,#1f1a14)" role="img" aria-label="Open bible on a table"><span>Bible Study</span></div>
    <div class="tile" style="left:310px;top:238px;width:390px;height:237px;background:linear-gradient(150deg,#8aa0b0,#3e4f5a)" role="img" aria-label="Seniors gathered together"><span>Seniors Ministry</span></div>
  </div>
  <div class="panel">
    <h2>GET INVOLVED</h2>
    <p>The success of our church depends on participation from people like you. Get involved in our ministries, it will change your life.</p>
  </div>
</section>

<section class="blog">
  <div class="text">
    <h2>LATEST BLOG</h2>
    <div class="date">Jan 21, 2019</div>
    <h3>PRAY WITHOUT CEASING</h3>
    <p>Lorem ipsum dolor sit amet, consectetur adipiscing elit, sed do eiusmod tempor incididunt ut labore et dolore magna aliqua. Ut enim ad minim veniam, quis nostrud exercitation ullamco laboris nisi ut aliquip ex ea commodo consequa.</p>
    <span class="btn">Read More</span>
  </div>
  <div class="photo" role="img" aria-label="Silhouette of a person praying against a sunset"></div>
</section>

<section class="pastor">
  <div class="left">
    <h2>PASTOR</h2>
    <div class="row">
      <div class="photo portrait" role="img" aria-label="Portrait of the pastor by the sea"></div>
      <blockquote>
        <h3>"One thing I asked of the Lord"</h3>
        <p>Lorem ipsum dolor sit amet, consectetur adipiscing elit, sed doei usmod tempor incididunt ut lab ore et dolore magna aliqua. Ut enim ad minim veniam, quis nos trud exercitation ullamco.</p>
        <cite>— Daniel Marsh —</cite>
      </blockquote>
    </div>
  </div>
  <div class="podcast">
    <h2>PODCAST</h2>
    <ul>
      <li><svg viewBox="0 0 30 30" fill="none" stroke="#fff" stroke-width="1.5"><rect x="1" y="1" width="28" height="28"/><path d="M12 9l9 6-9 6z" fill="#fff"/></svg><div><b>Holy Spirit : Strategy Thinking</b><small>by Daniel Marsh</small></div></li>
      <li><svg viewBox="0 0 30 30" fill="none" stroke="#fff" stroke-width="1.5"><rect x="1" y="1" width="28" height="28"/><path d="M12 9l9 6-9 6z" fill="#fff"/></svg><div><b>Holy Spirit : Strategy Thinking</b><small>by Daniel Marsh</small></div></li>
      <li><svg viewBox="0 0 30 30" fill="none" stroke="#fff" stroke-width="1.5"><rect x="1" y="1" width="28" height="28"/><path d="M12 9l9 6-9 6z" fill="#fff"/></svg><div><b>Holy Spirit : Strategy Thinking</b><small>by Daniel Marsh</small></div></li>
    </ul>
  </div>
</section>

<section class="events">
  <h2>UPCOMING EVENTS</h2>

  <div class="event-row">
    <div class="datebox"><svg viewBox="0 0 40 40" fill="none" stroke="#fff" stroke-width="2"><rect x="4" y="7" width="32" height="29"/><path d="M4 15h32M12 3v8M28 3v8M11 22h4M18 22h4M25 22h4M11 29h4M18 29h4"/></svg><div><b>22<sup>nd</sup></b><small>Feb 2019</small></div></div>
    <div class="info">
      <h3>Sharing our faith and love to children</h3>
      <div class="meta"><svg viewBox="0 0 14 14" fill="none" stroke="#474747"><circle cx="7" cy="7" r="6"/><path d="M7 3v4h3"/></svg>Thursday 08:00 - 09:00 am</div>
      <div class="meta"><svg viewBox="0 0 14 14" fill="none" stroke="#474747"><path d="M7 1C4.5 1 3 3 3 5c0 3 4 8 4 8s4-5 4-8c0-2-1.5-4-4-4z"/></svg>Wellspring Grace Community Church</div>
      <div class="meta"><svg viewBox="0 0 14 14" fill="none" stroke="#474747"><path d="M1 6l12-5-5 12-1-6z"/></svg>Elm Park, Riverside GA 30410</div>
    </div>
    <span class="btn">Read More</span>
  </div>

  <div class="event-row">
    <div class="datebox"><svg viewBox="0 0 40 40" fill="none" stroke="#fff" stroke-width="2"><rect x="4" y="7" width="32" height="29"/><path d="M4 15h32M12 3v8M28 3v8M11 22h4M18 22h4M25 22h4M11 29h4M18 29h4"/></svg><div><b>18<sup>th</sup></b><small>Feb 2019</small></div></div>
    <div class="info">
      <h3>Know Jesus Christ better through lines</h3>
      <div class="meta"><svg viewBox="0 0 14 14" fill="none" stroke="#474747"><circle cx="7" cy="7" r="6"/><path d="M7 3v4h3"/></svg>Thursday 08:00 - 09:00 am</div>
      <div class="meta"><svg viewBox="0 0 14 14" fill="none" stroke="#474747"><path d="M7 1C4.5 1 3 3 3 5c0 3 4 8 4 8s4-5 4-8c0-2-1.5-4-4-4z"/></svg>Wellspring Grace Community Church</div>
      <div class="meta"><svg viewBox="0 0 14 14" fill="none" stroke="#474747"><path d="M1 6l12-5-5 12-1-6z"/></svg>Elm Park, Riverside GA 30410</div>
    </div>
    <span class="btn">Read More</span>
  </div>

  <div class="event-row">
    <div class="datebox"><svg viewBox="0 0 40 40" fill="none" stroke="#fff" stroke-width="2"><rect x="4" y="7" width="32" height="29"/><path d="M4 15h32M12 3v8M28 3v8M11 22h4M18 22h4M25 22h4M11 29h4M18 29h4"/></svg><div><b>12<sup>th</sup></b><small>Feb 2019</small></div></div>
    <div class="info">
      <h3>Caring about the community and serving</h3>
      <div class="meta"><svg viewBox="0 0 14 14" fill="none" stroke="#474747"><circle cx="7" cy="7" r="6"/><path d="M7 3v4h3"/></svg>Thursday 08:00 - 09:00 am</div>
      <div class="meta"><svg viewBox="0 0 14 14" fill="none" stroke="#474747"><path d="M7 1C4.5 1 3 3 3 5c0 3 4 8 4 8s4-5 4-8c0-2-1.5-4-4-4z"/></svg>Wellspring Grace Community Church</div>
      <div class="meta"><svg viewBox="0 0 14 14" fill="none" stroke="#474747"><path d="M1 6l12-5-5 12-1-6z"/></svg>Elm Park, Riverside GA 30410</div>
    </div>
    <span class="btn">Read More</span>
  </div>
</section>

<footer class="footer">
  <div class="col">
    <h4>Latest Sermons</h4>
    <div class="item"><div class="photo thumb" style="background:linear-gradient(150deg,#6f8a5a,#2f3a2a)" role="img" aria-label="Sermon thumbnail of a child outdoors"></div><div><b>All things are possible</b><p>Lorem ipsum dolor sit amet, consectetur.</p></div></div>
    <div class="item"><div class="photo thumb" style="background:linear-gradient(150deg,#8a8a8a,#3a3a3a)" role="img" aria-label="Sermon thumbnail of hands holding a book"></div><div><b>Abounding the work of Lord</b><p>Lorem ipsum dolor sit amet, consectetur.</p></div></div>
  </div>
  <div class="col">
    <h4>Sermons Tags</h4>
    <div class="tags"><span>Faith</span><span>Forgiveness</span><span>Goodheartedness</span><span>Kindness</span><span>Love</span><span>Peace</span><span>Understanding</span></div>
    <div class="feed" role="img" aria-label="Landscape banner for the podcast feed">Podcast Feed</div>
  </div>
  <div class="col">
    <h4>Latest News</h4>
    <div class="item"><div class="photo thumb" style="background:linear-gradient(150deg,#9aa4ae,#3d434a)" role="img" aria-label="News thumbnail of a worship gathering"></div><div><b>Holy Spirit</b><p>Lorem ipsum dolor sit amet, consectetur.</p></div></div>
    <div class="item"><div class="photo thumb" style="background:linear-gradient(150deg,#c8a050,#3a2a1a)" role="img" aria-label="News thumbnail of candles in a church"></div><div><b>Holy Spirit</b><p>Lorem ipsum dolor sit amet, consectetur.</p></div></div>
  </div>
</footer>

<section class="bottom">
  <div>
    <div class="brand"><i class="dot"></i><span>WELLSPRING<small>GRACE COMMUNITY CHURCH</small></span></div>
    <div class="social"><i></i><i></i><i></i></div>
  </div>
  <ul><li>HOME</li><li>TEAM</li><li>FEATURES</li><li>EVENTS</li><li>SERMONS</li><li>CONTACT</li><li>BLOG</li><li><span class="btn btn-blue">Give Online</span></li></ul>
</section>

<div class="copyright">COPYRIGHT © 2019 WELLSPRING GRACE COMMUNITY CHURCH. ALL RIGHTS RESERVED.</div>

</body>
</html>
```